Business Card Design

We are a law firm which provides services to creditors.....we do collection litigation. I am wide open on suggestions. I was thinking of a square card? Alternatively, a vertically oriented standard card or a folded card.....something unique. I would like to use my firm logo and beyond that, I am open for any and all suggestions. I'm uncertain if the complete log is uploaded? If not, please let me email it to you.

Industry/Entity Type

Law Firm

Contact Information for Business Card

Hart, Crane & Dobbs, P.C.
Tom Dobbs, Lawyer
4387 N Larkspur Ave
Oklahoma City, OK 73924
tdobbs@HcdCounsel.com
www.HcdCounsel.com
mobile: 405-382-7914

```html
<!DOCTYPE html>
<html lang="en">
<head>
<meta charset="utf-8">
<title>Hart, Crane &amp; Dobbs, P.C. — Business Card</title>
<link rel="stylesheet" href="https://fonts.googleapis.com/css2?family=Arimo:wght@400;700&display=swap">
<style>
  :root {
    --backdrop: #e9e6e1;
    --paper: #ffffff;
    --paper-shade: #f1f1f1;
    --ink-grey: #4a4a4a;
    --ink-dark: #3a3a3a;
    --law-green: #12955a;
    --law-green-light: #3cc383;
    --law-green-deep: #0c7a47;
    --gold: #c9a437;
  }
  * { box-sizing: border-box; margin: 0; padding: 0; }
  html, body { width: 1200px; height: 885px; overflow: hidden; }
  body {
    background: var(--backdrop);
    font-family: "Arimo", Arial, sans-serif;
    position: relative;
  }
  .card {
    position: absolute;
    top: 118px;
    width: 380px;
    height: 650px;
    border-radius: 4px;
    overflow: hidden;
    box-shadow: 0 10px 30px rgba(0,0,0,.18);
  }

  /* Front */
  .card-front {
    left: 150px;
    background: linear-gradient(180deg, var(--paper) 0%, var(--paper-shade) 100%);
    text-align: center;
  }
  .brand-mark {
    margin: 62px auto 0;
    display: flex;
    align-items: center;
    justify-content: center;
    gap: 10px;
  }
  .brand-mark .dot {
    width: 18px; height: 18px;
    border-radius: 50%;
    background: var(--law-green);
  }
  .brand-mark .name {
    font-weight: 700;
    font-size: 19px;
    color: var(--law-green);
  }
  .firm-name {
    margin-top: 34px;
    font-weight: 700;
    font-size: 25px;
    color: var(--ink-grey);
    letter-spacing: .2px;
  }
  .person-name {
    margin-top: 44px;
    font-weight: 700;
    font-size: 42px;
    color: var(--law-green);
    line-height: 1;
  }
  .person-title {
    margin-top: 2px;
    font-weight: 700;
    font-size: 22px;
    color: var(--ink-grey);
  }
  .contact {
    margin-top: 30px;
    font-size: 21px;
    line-height: 1.4;
    color: var(--ink-dark);
    list-style: none;
  }
  .web-band {
    position: absolute;
    left: 0; right: 0; bottom: 0;
    height: 96px;
    background: linear-gradient(180deg, var(--law-green-light), var(--law-green));
    border-top: 4px solid var(--gold);
    display: flex;
    align-items: center;
    justify-content: center;
    color: #fff;
    font-size: 24px;
  }

  /* Back */
  .card-back {
    left: 670px;
    background: linear-gradient(160deg, var(--law-green-light) 0%, var(--law-green) 55%, var(--law-green-deep) 100%);
  }
  .card-back .faint-circle {
    position: absolute;
    left: 50%; top: 50%;
    width: 260px; height: 260px;
    margin: -130px 0 0 -130px;
    border-radius: 50%;
    background: rgba(255,255,255,.08);
  }
  .card-back .firm-name-back {
    position: absolute;
    left: 50%; top: 50%;
    transform: translate(-50%, -50%) rotate(90deg);
    white-space: nowrap;
    color: #fff;
    font-weight: 700;
    font-size: 40px;
  }
</style>
</head>
<body>
  <section class="card card-front">
    <div class="brand-mark">
      <span class="dot"></span>
      <span class="name">Hart, Crane &amp; Dobbs</span>
    </div>
    <h1 class="firm-name">Hart, Crane &amp; Dobbs, P.C.</h1>
    <h2 class="person-name">Tom Dobbs</h2>
    <p class="person-title">Lawyer</p>
    <ul class="contact">
      <li>405-382-7914</li>
      <li>tdobbs@HcdCounsel.com</li>
      <li>4387 N Larkspur Ave</li>
      <li>Oklahoma City, OK 73924</li>
    </ul>
    <div class="web-band">www.HcdCounsel.com</div>
  </section>

  <section class="card card-back">
    <div class="faint-circle"></div>
    <p class="firm-name-back">Hart, Crane &amp; Dobbs, P.C.</p>
  </section>
</body>
</html>
```